KLV Plant Services

We are a heavy diesel mechanical business with additional air con certificates, remapping engine rebuilt

Contact Information for Business Card

Company Name, Director Name, Managing Director, Contact details, email and website

Font styles to use
Serif
Script

```html
<!DOCTYPE html>
<html lang="en">
<head>
<meta charset="utf-8">
<title>KLV Plant Services – Business Card</title>
<link href="https://fonts.googleapis.com/css2?family=Arimo:wght@400;700&display=swap" rel="stylesheet">
<style>
  :root {
    --backdrop: #7b7b7b;
    --card-black: #050505;
    --card-white: #f3f3f5;
    --navy: #1c1f78;
    --ink: #222228;
    --muted: #55555c;
    --logo-dim: #3c3c3c;
    --light-text: #e8e8e8;
  }
  * { margin: 0; padding: 0; box-sizing: border-box; }
  html, body {
    width: 1200px; height: 900px; overflow: hidden;
    background: var(--backdrop);
    font-family: "Arimo", Arial, sans-serif;
  }
  .canvas {
    position: relative; width: 1200px; height: 900px;
  }
  .card {
    position: absolute; left: 270px;
    width: 660px; height: 377px;
    border-radius: 26px; overflow: hidden;
    box-shadow: 0 10px 24px rgba(0,0,0,.35);
  }
  /* Back side */
  .card-back { top: 48px; background: var(--card-black); }
  .back-brand {
    position: absolute; left: 0; right: 0; top: 130px;
    display: flex; align-items: center; justify-content: center; gap: 14px;
  }
  .brand-dot {
    width: 34px; height: 34px; border-radius: 50%;
    background: var(--logo-dim);
  }
  .back-brand .brand-name {
    color: var(--logo-dim); font-weight: 700; font-size: 40px; letter-spacing: .5px;
  }
  .back-web {
    position: absolute; left: 0; right: 0; top: 290px;
    text-align: center; color: var(--light-text);
    font-size: 15px; letter-spacing: 4px;
  }
  /* Front side */
  .card-front { top: 475px; background: var(--card-white); }
  .front-shape { position: absolute; inset: 0; }
  .front-brand {
    position: absolute; left: 40px; top: 62px;
    display: flex; align-items: center; gap: 10px;
  }
  .front-brand .brand-dot { width: 24px; height: 24px; background: var(--navy); }
  .front-brand .brand-name {
    color: var(--navy); font-weight: 700; font-size: 27px;
  }
  .address {
    position: absolute; left: 40px; top: 170px;
    color: var(--ink); font-size: 15px; line-height: 20px;
  }
  .contact-list {
    position: absolute; left: 40px; top: 236px; list-style: none;
    color: var(--ink); font-size: 15px; line-height: 22px;
  }
  .contact-list li { display: flex; align-items: center; gap: 9px; }
  .contact-list svg { width: 13px; height: 13px; fill: var(--navy); flex: none; }
  .person {
    position: absolute; left: 400px; top: 150px; text-align: left;
  }
  .person-name { color: var(--navy); font-weight: 700; font-size: 24px; }
  .person-role { color: var(--muted); font-size: 15px; margin-top: 4px; }
</style>
</head>
<body>
<main class="canvas">
  <section class="card card-back" aria-label="Card back">
    <div class="back-brand">
      <span class="brand-dot"></span>
      <span class="brand-name">KLV Plant Services</span>
    </div>
    <p class="back-web">www.klvplant.com</p>
  </section>

  <section class="card card-front" aria-label="Card front">
    <svg class="front-shape" width="660" height="377" viewBox="0 0 660 377" aria-hidden="true">
      <rect x="470" y="0" width="190" height="377" fill="var(--card-black)"/>
      <ellipse cx="482" cy="188" rx="202" ry="216" fill="var(--card-black)"/>
      <circle cx="468" cy="188" r="200" fill="var(--card-white)"/>
    </svg>

    <div class="front-brand">
      <span class="brand-dot"></span>
      <span class="brand-name">KLV Plant Services</span>
    </div>

    <p class="address">4120 Harbor Lane<br>Riverton, NJ 08077</p>

    <ul class="contact-list">
      <li>
        <svg viewBox="0 0 24 24"><path d="M6.6 10.8a15.1 15.1 0 0 0 6.6 6.6l2.2-2.2c.3-.3.7-.4 1-.2 1.1.4 2.3.6 3.6.6.6 0 1 .4 1 1V20c0 .6-.4 1-1 1A17 17 0 0 1 3 4c0-.6.4-1 1-1h3.5c.6 0 1 .4 1 1 0 1.3.2 2.5.6 3.6.1.3 0 .7-.2 1z"/></svg>
        (555) 0142-3378
      </li>
      <li>
        <svg viewBox="0 0 24 24"><path d="M2 5h20v14H2z M3 6l9 7 9-7" /></svg>
        name@klvplant.com
      </li>
      <li>
        <svg viewBox="0 0 24 24"><circle cx="12" cy="12" r="10"/></svg>
        www.klvplant.com
      </li>
    </ul>

    <div class="person">
      <p class="person-name">Daniel Hart</p>
      <p class="person-role">Managing Director</p>
    </div>
  </section>
</main>
</body>
</html>
```